Business Card for premium dental clinic

We are a premium dental clinic based in Brasov, Romania with more than 15 year on the market, providing quality dental treatment made by a team of more specialized dentists, working with modern equipment as a solution to beautiful and healthy teeth.

Our current logo for the clinic use 2 square with colors black and gold - dr Ternisu - studio, using family fonts Bodoni, Myriad Pro and Segoe Print.
Depending on the printing we used some gold CMYK background or gold foil picture background or a gold gradient.
We want a business card:
- eye catching business card
- distinguished business card
- premium design
- to keep the color scheme of black and gold
- to attract the customers to spent time reading the information
- modern concept

```html
<!DOCTYPE html>
<html lang="en">
<head>
<meta charset="utf-8">
<title>dr Ternisu – Business Card</title>
<link rel="stylesheet" href="https://fonts.googleapis.com/css2?family=Montserrat:wght@400;500&display=swap">
<style>
  :root {
    --backdrop: #e9e6e1;
    --card-black: #1e1e1e;
    --card-white: #ffffff;
    --gold: #f2cf2e;
    --gold-deep: #c9a227;
    --ink-grey: #555555;
    --shadow: 0 14px 30px rgba(0, 0, 0, 0.22);
  }
  * { box-sizing: border-box; margin: 0; padding: 0; }
  html, body {
    width: 1200px;
    height: 716px;
    overflow: hidden;
    background: var(--backdrop);
    font-family: "Montserrat", sans-serif;
  }
  .canvas {
    position: relative;
    width: 1200px;
    height: 716px;
  }
  .card {
    position: absolute;
    top: 208px;
    width: 500px;
    height: 300px;
    border-radius: 6px;
    box-shadow: var(--shadow);
  }
  .card--front {
    left: 60px;
    background: var(--card-black);
    border: 2px solid var(--gold-deep);
  }
  .card--back {
    left: 640px;
    background: var(--card-white);
  }

  /* clinic name mark */
  .brand {
    position: absolute;
    display: flex;
    align-items: center;
    gap: 12px;
  }
  .brand__square {
    width: 26px;
    height: 26px;
    background: var(--gold);
  }
  .brand__name {
    font-weight: 500;
    font-size: 30px;
    color: var(--gold);
    letter-spacing: 0.5px;
  }
  .card--front .brand {
    left: 50%;
    top: 50%;
    transform: translate(-50%, -50%);
  }
  .card--back .brand {
    left: 40px;
    top: 44px;
  }

  /* contact block */
  .contact {
    position: absolute;
    right: 40px;
    bottom: 34px;
    text-align: left;
    color: var(--ink-grey);
    font-size: 13px;
    line-height: 1.55;
  }
  .contact__name {
    color: var(--gold);
    font-size: 22px;
    font-weight: 500;
    letter-spacing: 1px;
    margin-bottom: 6px;
  }
  .contact__line {
    display: flex;
    align-items: center;
    gap: 7px;
  }
  .contact__icon {
    width: 10px;
    height: 10px;
    flex: none;
  }
  .contact__address { margin-top: 4px; }
</style>
</head>
<body>
<main class="canvas">

  <section class="card card--front" aria-label="Card front">
    <div class="brand">
      <span class="brand__square"></span>
      <span class="brand__name">dr Ternisu</span>
    </div>
  </section>

  <section class="card card--back" aria-label="Card back">
    <div class="brand">
      <span class="brand__square"></span>
      <span class="brand__name">dr Ternisu</span>
    </div>

    <div class="contact">
      <p class="contact__name">DR TERNISU</p>
      <p class="contact__line">
        <svg class="contact__icon" viewBox="0 0 10 10" aria-hidden="true"><path d="M2 1 L4 1 L4.6 3 L3.5 4 Q4.5 6 6 6.5 L7 5.4 L9 6 L9 8 Q5 9 2.5 6 Q1 4 2 1Z" fill="var(--gold)"/></svg>
        +40 268 555 019
      </p>
      <p class="contact__line">
        <svg class="contact__icon" viewBox="0 0 10 10" aria-hidden="true"><rect x="0.8" y="2" width="8.4" height="6" fill="none" stroke="var(--gold)" stroke-width="1"/><path d="M0.8 2 L5 5.4 L9.2 2" fill="none" stroke="var(--gold)" stroke-width="1"/></svg>
        info@drternisu.ro
      </p>
      <p class="contact__line">
        <svg class="contact__icon" viewBox="0 0 10 10" aria-hidden="true"><circle cx="5" cy="5" r="4" fill="none" stroke="var(--gold)" stroke-width="1"/><path d="M1 5 H9 M5 1 Q2.5 5 5 9 M5 1 Q7.5 5 5 9" fill="none" stroke="var(--gold)" stroke-width="0.8"/></svg>
        www.drternisu.ro
      </p>
      <p class="contact__address">Strada Livezii 24,<br>Brașov 500210, Romania</p>
    </div>
  </section>

</main>
</body>
</html>
```